BRELWINCare.co.uk - Mental Health Clinic for Child and Adolescents

Updated 29/01/2018***
I am not sure you guys are getting the idea regards to the opening page / homescreen layout. Can you look at the new images I have uploaded (page 5, 6 and 7) These are some of the layouts I like but to incorporate my chosen images, with the BRELWIN commissioner, buttons and a sliding header bar.
I have written a strong brief, I am looking for a website, preferably wordpress as i know they are easy to maintain. I am looking for a one page site, with the top / opening page being full screen image with drop down categories. I have made a rough design, see full brief in word doc attached, there is some freedom to play around with the design aspect but it will need to relay all the content provided. I like a minimal feel. I have also attached some images that may be useful, but will need a new logo for BRELWIN Care. I have attached some logo idea's, it is up to you decide whether you want to use them.
I would prefer the homepage as full screen image, and the categories offered as a drop down or over the main image.
I have also attached linked to some competitors websites:
https://www.vorimant-health.co.uk/
http://www.qlbn.org.uk/
Industry/Entity Type
Clinic
Number of Pages Required
1 page
Font styles to use
Look and feel
Each slider illustrates characteristics of the customer's brand and the style your logo design should communicate.

```html
<!DOCTYPE html>
<html lang="en">
<head>
<meta charset="utf-8">
<title>BRELWIN Care – Child &amp; Adolescent Clinic</title>
<link rel="stylesheet" href="https://fonts.googleapis.com/css2?family=Comfortaa:wght@400;700&family=Open+Sans:wght@400;600;700&family=Noto+Serif:ital@1&display=swap">
<style>
:root{
  --purple:#5f2571;
  --purple-line:#74408a;
  --teal:#0f9480;
  --text:#666;
  --heading:#3d3d3d;
  --footer-bg:#f4f4f4;
  --white:#fff;
}
*{box-sizing:border-box;margin:0;padding:0}
html,body{width:763px;height:1200px;overflow:hidden;background:var(--white)}
body{position:relative;font-family:"Open Sans",Arial,sans-serif;color:var(--text)}
.sidebar{position:absolute;left:0;top:0;width:161px;height:1200px;background:var(--purple)}
.brand{height:110px;background:var(--white);text-align:center;padding-top:28px}
.brand-name{font-family:"Comfortaa",sans-serif;font-weight:700;font-size:24px;color:var(--purple);letter-spacing:.5px;white-space:nowrap}
.brand-line{font-family:"Open Sans",sans-serif;font-weight:400;font-size:10px;color:var(--text);margin-top:9px;white-space:nowrap}
.main-nav{list-style:none;padding:0 8px 0 5px}
.main-nav li{border-bottom:1px solid var(--purple-line);height:26.7px;line-height:26.7px;padding-left:20px;font-family:"Comfortaa",sans-serif;font-weight:700;font-size:8.5px;color:var(--white);text-transform:uppercase}
.hero{position:absolute;left:161px;top:0;width:602px;height:358px;background:linear-gradient(120deg,#d9d4cc 0%,#efece7 40%,#b9b2a8 75%,#8d8478 100%)}
.hero-card{position:absolute;left:168px;top:194px;width:268px;height:138px;background:rgba(110,110,110,.55);text-align:center;color:var(--white)}
.hero-title{font-family:"Comfortaa",sans-serif;font-size:23px;margin-top:16px;letter-spacing:.5px}
.hero-text{font-family:Arial,sans-serif;font-size:7.5px;line-height:15px;margin:9px 14px 0}
.btn{position:absolute;top:90px;height:28px;border-radius:14px;font-family:"Comfortaa",sans-serif;font-weight:700;font-size:10px;line-height:28px;color:var(--white)}
.btn-parents{left:20px;width:112px;background:var(--teal)}
.btn-commissioners{left:136px;width:113px;background:var(--purple)}
.quote-band{position:absolute;left:161px;top:358px;width:602px;height:72px;background:var(--teal);color:var(--white);text-align:center;font-family:"Comfortaa",sans-serif;font-weight:700;font-size:13.5px;line-height:72px}
.quote-band svg{position:absolute;top:17px}
.welcome-title{position:absolute;left:175px;top:475px;font-family:"Comfortaa",sans-serif;font-weight:700;font-size:17px;color:var(--teal);letter-spacing:.3px}
.welcome-text{position:absolute;left:175px;top:519px;width:315px;font-family:Arial,sans-serif;font-size:7.3px;line-height:17.5px;color:var(--text)}
.welcome-photo{position:absolute;left:522px;top:461px;width:208px;height:208px;border-radius:50%;border:2px solid #ddd;background:linear-gradient(160deg,#f1efec 0%,#d8d2cb 45%,#6c7a78 75%,#4f5c5c 100%)}
.divider{position:absolute;left:173px;top:690px;width:578px;height:1px;background:#e2e2e2}
.blog-title{position:absolute;left:161px;width:602px;top:702px;text-align:center;font-family:"Comfortaa",sans-serif;font-weight:700;font-size:21px;color:var(--teal);letter-spacing:.5px}
.post{position:absolute;top:747px;width:187px}
.post-photo{height:122px;background:linear-gradient(135deg,#e6e1da,#c9bfb3 55%,#8f8a84)}
.post h3{font-family:"Comfortaa",sans-serif;font-weight:400;font-size:11px;color:var(--heading);margin-top:13px;letter-spacing:.3px}
.post p{font-family:Arial,sans-serif;font-size:7.3px;line-height:16.5px;margin-top:8px;color:var(--text)}
.post-meta{margin-top:10px;font-family:"Noto Serif",serif;font-style:italic;font-size:7.8px;color:var(--teal);display:flex;align-items:center;gap:4px}
.post-meta svg{flex:none}
.footer{position:absolute;left:161px;top:1003px;width:602px;height:154px;background:var(--footer-bg)}
.footer-brand{position:absolute;left:24px;top:50px;width:236px;text-align:center}
.footer-brand .brand-name{font-size:30px}
.footer-brand .brand-line{font-size:12px;margin-top:12px}
.footer h4{font-family:Arial,sans-serif;font-weight:700;font-size:10.5px;color:var(--purple);text-transform:uppercase}
.contact{position:absolute;left:246px;top:27px;width:160px}
.contact li{list-style:none;display:flex;gap:7px;font-family:Arial,sans-serif;font-size:7.3px;color:#777;margin-top:10px;line-height:9.5px}
.contact li:first-child{margin-top:17px}
.contact li svg{flex:none;margin-top:1px}
.contact a{color:#777}
.newsletter{position:absolute;left:427px;top:27px;width:160px}
.newsletter p{font-family:Arial,sans-serif;font-size:7.3px;line-height:13px;color:#888;margin-top:14px}
.email-field{margin-top:9px;width:146px;height:22px;border:1px solid #ddd;background:var(--white);font-size:7.5px;line-height:20px;padding-left:10px;color:#666}
.subscribe{margin-top:6px;display:inline-block;background:var(--purple);color:var(--white);font-size:7px;font-weight:700;height:18px;line-height:18px;padding:0 7px}
.copyright{position:absolute;left:161px;top:1157px;width:602px;height:43px;background:var(--purple);color:var(--white);font-family:Arial,sans-serif;font-size:7.3px;text-align:center;line-height:43px}
</style>
</head>
<body>
<aside class="sidebar">
  <div class="brand">
    <div class="brand-name">BRELWIN</div>
    <div class="brand-line">Child &amp; Adolescent Clinic</div>
  </div>
  <ul class="main-nav">
    <li>About Us</li><li>Our Team</li><li>Our Services</li><li>Contact Us</li>
    <li>Parents</li><li>Commissioners</li><li>Blog</li><li>Forum</li>
  </ul>
</aside>

<section class="hero" role="img" aria-label="Clinician in a white blouse talking with a young boy in a checked shirt in a bright room">
  <div class="hero-card">
    <div class="hero-title">BRELWIN Care</div>
    <p class="hero-text">We have a turnaround time of 24 hours for all ADHD and ASD screening, and aim to have see any child</p>
    <div class="btn btn-parents">Parents</div>
    <div class="btn btn-commissioners">Commissioners</div>
  </div>
</section>

<div class="quote-band">
  <svg style="left:30px" width="12" height="38" viewBox="0 0 12 38"><polyline points="11,1 1,19 11,37" fill="none" stroke="#fff" stroke-width="1"/></svg>
  “ADHD &amp; Autism Screening within 24 Hours”
  <svg style="right:30px" width="12" height="38" viewBox="0 0 12 38"><polyline points="1,1 11,19 1,37" fill="none" stroke="#fff" stroke-width="1"/></svg>
</div>

<h2 class="welcome-title">Welcome to BRELWIN Care</h2>
<p class="welcome-text">BRELWIN Care was formed with a vision to provide the very best BRELWIN assessments, therapy and aftercare. We have unique modern pathways that allow children and adolescents to be seen quickly by handpicked clinicians that are highly skilled and some of the best in their chosen field. We have a turnaround time of 24 hours for all ADHD and ASD screening, and aim to have see any child for a full ASD, or ADHD assessment within 14 days. If your child has been diagnosed with ADHD or ASD we offer the very best post diagnosis support to both the child and family.</p>
<div class="welcome-photo" role="img" aria-label="Group of five smiling teenagers sitting together on a sofa"></div>

<div class="divider"></div>
<h2 class="blog-title">Latest Blog</h2>

<article class="post" style="left:174px">
  <div class="post-photo" role="img" aria-label="Clinician talking with a boy in a bright room"></div>
  <h3>Contrary to Popular</h3>
  <p>Sed ut perspiciatis unde omnis iste natus error sit voluptatem accusantium doloremque laudantium, inventore vitae dicta sunt explicabo.</p>
  <div class="post-meta"><svg width="8" height="8" viewBox="0 0 8 8"><rect x=".5" y="1.5" width="7" height="6" fill="none" stroke="#0f9480"/><line x1="2" y1="0" x2="2" y2="2" stroke="#0f9480"/><line x1="6" y1="0" x2="6" y2="2" stroke="#0f9480"/></svg>1 month ago&nbsp;&nbsp;<svg width="9" height="8" viewBox="0 0 9 8"><ellipse cx="4.5" cy="3.5" rx="4" ry="3" fill="none" stroke="#0f9480"/></svg>05 Comments</div>
</article>
<article class="post" style="left:370px">
  <div class="post-photo" role="img" aria-label="Therapist in conversation with a young girl"></div>
  <h3>Contrary to Popular</h3>
  <p>Sed ut perspiciatis unde omnis iste natus error sit voluptatem accusantium doloremque laudantium, inventore vitae dicta sunt explicabo.</p>
  <div class="post-meta"><svg width="8" height="8" viewBox="0 0 8 8"><rect x=".5" y="1.5" width="7" height="6" fill="none" stroke="#0f9480"/><line x1="2" y1="0" x2="2" y2="2" stroke="#0f9480"/><line x1="6" y1="0" x2="6" y2="2" stroke="#0f9480"/></svg>1 month ago&nbsp;&nbsp;<svg width="9" height="8" viewBox="0 0 9 8"><ellipse cx="4.5" cy="3.5" rx="4" ry="3" fill="none" stroke="#0f9480"/></svg>05 Comments</div>
</article>
<article class="post" style="left:566px">
  <div class="post-photo" role="img" aria-label="Teenage boy in a hoodie sitting in a consultation room"></div>
  <h3>Contrary to Popular</h3>
  <p>Sed ut perspiciatis unde omnis iste natus error sit voluptatem accusantium doloremque laudantium, inventore vitae dicta sunt explicabo.</p>
  <div class="post-meta"><svg width="8" height="8" viewBox="0 0 8 8"><rect x=".5" y="1.5" width="7" height="6" fill="none" stroke="#0f9480"/><line x1="2" y1="0" x2="2" y2="2" stroke="#0f9480"/><line x1="6" y1="0" x2="6" y2="2" stroke="#0f9480"/></svg>1 month ago&nbsp;&nbsp;<svg width="9" height="8" viewBox="0 0 9 8"><ellipse cx="4.5" cy="3.5" rx="4" ry="3" fill="none" stroke="#0f9480"/></svg>05 Comments</div>
</article>

<footer class="footer">
  <div class="footer-brand">
    <div class="brand-name">BRELWIN</div>
    <div class="brand-line">Child &amp; Adolescent Clinic</div>
  </div>
  <div class="contact">
    <h4>Contact Us</h4>
    <ul>
      <li><svg width="9" height="7" viewBox="0 0 9 7"><path d="M0 2 Q4.5 -1 9 2 L8 3 L6 2.5 L6 1.8 Q4.5 1.3 3 1.8 L3 2.5 L1 3Z M1.5 4 H7.5 V7 H1.5Z" fill="#999"/></svg>0203 555 0172&nbsp;&nbsp;(Phone)</li>
      <li><svg width="9" height="8" viewBox="0 0 9 8"><rect x="2" y="0" width="5" height="3" fill="none" stroke="#999"/><rect x="0" y="3" width="9" height="5" fill="#999"/></svg>0203 555 0172&nbsp;&nbsp;&nbsp;(Fax)</li>
      <li><svg width="9" height="7" viewBox="0 0 9 7"><rect x=".5" y=".5" width="8" height="6" fill="none" stroke="#999"/><polyline points=".5,.5 4.5,4 8.5,.5" fill="none" stroke="#999"/></svg><a>enquiry@brelwincare.co.uk</a></li>
      <li><svg width="7" height="9" viewBox="0 0 7 9"><path d="M3.5 9 L0.6 4.5 A3.2 3.2 0 1 1 6.4 4.5Z" fill="#999"/><circle cx="3.5" cy="3.2" r="1.2" fill="#f4f4f4"/></svg>Ashdown Suite 2B, 41-47 Mill Lane,<br>London, E17 4RT</li>
    </ul>
  </div>
  <div class="newsletter">
    <h4>Newsletter</h4>
    <p>Register Your email address to get information about us</p>
    <div class="email-field">Email Address</div>
    <div class="subscribe">SUBSCRIBE</div>
  </div>
</footer>
<div class="copyright">© Copyright 2018 BRELWIN Care.All Rights Reserved</div>
</body>
</html>
```